Calendar Design Project: 2025 with Specific Edits

This is a straightforward project where your creativity can shine!
Simply take the existing 2024 calendar and adapt it for 2025 by incorporating the new photos I've attached.
Please keep the overall concept of the 2024 calendar intact—your focus will be on enhancing it with fresh visuals.

I can't wait to see your amazing designs!
I am looking for a talented graphic designer to create a new 2025 calendar with specific adjustments.
Pictures attached.
Requirements:
Calendar Size: 52cm x 34cm
March Folder:
Adjust the image named "attached - DJI-0025" to make the circular road darker to match the rest of the design.
May Folder:
Modify the circled area in the May image to ensure it looks consistent with the other road (reference file: "attached - After").
November Folder:
Clear out the circled area in the November image (reference file: "attached - After1").
Please let me know if you have any questions or need further clarification.
I added to my breif a design i made last year for same client.
2025, calendar should be vertical and not horizontal. and some of the photos attache are "Before" and "After" please include together inside each month of the calendar.
Thank you!
Feel free to adjust any details as necessary!

Hello talented designers!

I’m excited to share that this is my 14th project on the ArtHive platform, and I’ve been fortunate to have successful collaborations in the past. I'm looking forward to creating a new 2025 calendar with your help, and I believe that with your creativity and skills, we can make this project a success as well!

I hope to establish a long-term relationship with a talented team like yours. As an added incentive, I will be offering a bonus for the winner, and I may select more than one winner, so everyone has a chance to shine!

Let’s make something amazing together!

Best
Update:
cancel or before, only place the After picture

Requirements
Must have
• Project Overview Objective: Create a 2025 calendar using the provided images, maintaining the design concept from the 2024 calendar but enhancing it with new visuals. Format: Vertical layout (52cm x 34cm).

```html
<!DOCTYPE html>
<html lang="en">
<head>
<meta charset="utf-8">
<title>Verda Construction Ltd – Calendar 2025 – February</title>
<link href="https://fonts.googleapis.com/css2?family=Open+Sans:wght@400;600;700&family=Roboto+Condensed:wght@400;700&display=swap" rel="stylesheet">
<style>
  :root{
    --green-bright:#8cf51c;
    --green-soft:#d9f7b6;
    --green-text:#5fe35a;
    --cell-green:#c7f6a9;
    --cell-grey:#eef0f1;
    --ink:#151515;
    --ink-muted:#5a5f5e;
    --paper:#ffffff;
  }
  *{margin:0;padding:0;box-sizing:border-box}
  html,body{width:848px;height:1200px;overflow:hidden;background:var(--paper)}
  body{font-family:"Open Sans",Arial,sans-serif;color:var(--ink)}
  .page{position:relative;width:848px;height:1200px;overflow:hidden;background:var(--paper)}

  .hero-photo{position:absolute;left:0;top:95px;width:848px;height:440px;
    background:linear-gradient(180deg,#bfe0ee 0%,#9fb59a 18%,#a8917f 40%,#8f8d8c 60%,#3a4fa0 75%,#b9a28a 100%)}
  .hero-waves{position:absolute;left:0;top:0;width:848px;height:640px}

  .brand{position:absolute;left:78px;top:58px;display:flex;align-items:center;gap:10px}
  .brand-mark{width:26px;height:26px;background:var(--ink)}
  .brand-name{font-family:"Roboto Condensed",Arial,sans-serif;font-weight:700;font-size:44px;line-height:1;color:var(--ink);letter-spacing:1px}
  .brand-sub{position:absolute;left:80px;top:110px;font-family:"Roboto Condensed",Arial,sans-serif;font-size:19px;color:var(--ink);letter-spacing:.5px}

  .project-caption{position:absolute;left:243px;top:541px;width:370px;height:78px;border-radius:12px;
    background:rgba(255,255,255,.45);padding-top:10px;text-align:center;
    font-size:11.3px;font-weight:600;line-height:17px;letter-spacing:-.3px;color:var(--ink)}

  .title-kicker{position:absolute;left:41px;top:636px;font-size:31px;line-height:1;color:var(--green-text);letter-spacing:.5px}
  .title-year{position:absolute;left:39px;top:673px;font-size:62px;line-height:1;color:var(--ink)}
  .month-name{position:absolute;left:375px;top:703px;font-size:44px;line-height:1;font-weight:400;color:var(--ink-muted);letter-spacing:1px}

  .month-grid{position:absolute;left:40px;top:770px;display:grid;
    grid-template-columns:repeat(7,76px);column-gap:5.4px;
    grid-template-rows:40px repeat(5,51px);row-gap:11.5px}
  .month-grid .day-head{display:flex;align-items:center;justify-content:center;font-size:10.5px;font-weight:600;background:var(--cell-grey)}
  .month-grid .day{background:var(--cell-grey);font-size:26px;display:flex;align-items:flex-end;padding:0 0 3px 10px;line-height:1}
  .month-grid .weekend{background:var(--cell-green)}

  .mini{position:absolute;left:620px;width:192px}
  .mini-title{font-size:12px;color:var(--ink-muted);letter-spacing:.3px}
  .mini-title span{color:var(--green-text)}
  .mini-grid{margin-top:3px;display:grid;grid-template-columns:repeat(7,25px);column-gap:2.8px;grid-auto-rows:15px;row-gap:6.8px}
  .mini-grid .mh{height:12px;font-size:3.6px;font-weight:700;display:flex;align-items:center;justify-content:center;background:var(--cell-grey)}
  .mini-grid .md{background:var(--cell-grey);font-size:9px;display:flex;align-items:center;padding-left:3px}
  .mini-grid .mw{background:var(--cell-green)}
  .mini-jan{top:766px}
  .mini-mar{top:985px}

  .footer{position:absolute;left:45px;top:1150px;width:770px;display:flex;align-items:center;
    font-family:"Roboto Condensed",Arial,sans-serif;font-size:9.6px;color:var(--ink-muted)}
  .footer-brand{width:96px;line-height:1}
  .footer-brand .name{font-weight:700;font-size:18px;color:var(--ink)}
  .footer-brand .sub{font-size:6.5px;color:var(--ink)}
  .footer-item{margin-left:18px;white-space:nowrap}
  .footer-item b{color:var(--green-text);font-weight:700}
</style>
</head>
<body>
<main class="page">
  <div class="hero-photo" role="img" aria-label="Aerial photo of highway reconstruction: a yellow tipper truck feeding an asphalt paver on a fresh dark lane, workers in high-visibility vests, a roller and the parallel carriageway beside red earth and green bush"></div>

  <svg class="hero-waves" viewBox="0 0 848 640" preserveAspectRatio="none" aria-hidden="true">
    <defs>
      <linearGradient id="greenTop" x1="0" y1="0" x2="1" y2="0.3">
        <stop offset="0" stop-color="#eafad8"/>
        <stop offset="0.55" stop-color="#b6f26a"/>
        <stop offset="1" stop-color="#8cf51c"/>
      </linearGradient>
      <linearGradient id="greenBottom" x1="0" y1="1" x2="1" y2="0">
        <stop offset="0" stop-color="#ffffff"/>
        <stop offset="0.45" stop-color="#d7f8ad"/>
        <stop offset="1" stop-color="#8cf51c"/>
      </linearGradient>
    </defs>
    <path d="M0 0 H848 V88 C700 60 560 110 420 140 C290 168 150 190 0 172 Z" fill="url(#greenTop)"/>
    <path d="M0 0 H848 V6 C600 40 300 10 40 0 Z" fill="#ffffff" opacity=".7"/>
    <path d="M0 100 C150 150 320 125 470 100 C620 75 740 40 848 44 V20 C720 20 600 55 460 80 C300 110 150 120 0 85 Z" fill="#ffffff" opacity=".55"/>
    <path d="M0 532 C200 520 400 500 560 505 C700 500 790 470 848 455 V640 H0 Z" fill="url(#greenBottom)"/>
    <path d="M0 560 C200 590 420 600 600 610 C720 618 800 625 848 628 V640 H0 Z" fill="#ffffff"/>
  </svg>

  <div class="brand"><span class="brand-mark"></span><span class="brand-name">VERDA</span></div>
  <div class="brand-sub">CONSTRUCTION LTD</div>

  <p class="project-caption">RESURFACING OF EXISTING CARRIAGEWAY AND CONSTRUCTION<br>OF NEW SHOULDERS ON DUALIZATION OF<br>NORTHGATE -RIVERBEND EXPRESSWAY</p>

  <div class="title-kicker">CALENDAR</div>
  <div class="title-year">2025</div>
  <h1 class="month-name">FEBRUARY</h1>

  <section class="month-grid" aria-label="February 2025">
    <div class="day-head weekend">SUNDAY</div><div class="day-head">MONDAY</div><div class="day-head">TUESDAY</div><div class="day-head">WEDNESDAY</div><div class="day-head">THURSDAY</div><div class="day-head">FRIDAY</div><div class="day-head weekend">SATURDAY</div>
    <div class="day weekend"></div><div class="day"></div><div class="day"></div><div class="day"></div><div class="day"></div><div class="day"></div><div class="day weekend">1</div>
    <div class="day weekend">2</div><div class="day">3</div><div class="day">4</div><div class="day">5</div><div class="day">6</div><div class="day">7</div><div class="day weekend">8</div>
    <div class="day weekend">9</div><div class="day">10</div><div class="day">11</div><div class="day">12</div><div class="day">13</div><div class="day">14</div><div class="day weekend">15</div>
    <div class="day weekend">16</div><div class="day">17</div><div class="day">18</div><div class="day">19</div><div class="day">20</div><div class="day">21</div><div class="day weekend">22</div>
    <div class="day weekend">23</div><div class="day">24</div><div class="day">25</div><div class="day">26</div><div class="day">17</div><div class="day">28</div><div class="day weekend"></div>
  </section>

  <section class="mini mini-jan" aria-label="January 2025">
    <div class="mini-title">JANUARY &nbsp;| &nbsp;<span>2025</span></div>
    <div class="mini-grid">
      <div class="mh mw">SUNDAY</div><div class="mh">MONDAY</div><div class="mh">TUESDAY</div><div class="mh">WEDNESDAY</div><div class="mh">THURSDAY</div><div class="mh">FRIDAY</div><div class="mh mw">SATURDAY</div>
      <div class="md mw"></div><div class="md"></div><div class="md"></div><div class="md">1</div><div class="md">2</div><div class="md">3</div><div class="md mw">4</div>
      <div class="md mw">5</div><div class="md">6</div><div class="md">7</div><div class="md">8</div><div class="md">9</div><div class="md">10</div><div class="md mw">11</div>
      <div class="md mw">12</div><div class="md">13</div><div class="md">14</div><div class="md">15</div><div class="md">16</div><div class="md">17</div><div class="md mw">18</div>
      <div class="md mw">19</div><div class="md">20</div><div class="md">21</div><div class="md">22</div><div class="md">23</div><div class="md">24</div><div class="md mw">25</div>
      <div class="md mw">26</div><div class="md">27</div><div class="md">28</div><div class="md">29</div><div class="md">30</div><div class="md">31</div><div class="md mw"></div>
    </div>
  </section>

  <section class="mini mini-mar" aria-label="March 2025">
    <div class="mini-title">MARCH &nbsp;| &nbsp;<span>2025</span></div>
    <div class="mini-grid">
      <div class="mh mw">SUNDAY</div><div class="mh">MONDAY</div><div class="mh">TUESDAY</div><div class="mh">WEDNESDAY</div><div class="mh">THURSDAY</div><div class="mh">FRIDAY</div><div class="mh mw">SATURDAY</div>
      <div class="md mw">30</div><div class="md">31</div><div class="md"></div><div class="md"></div><div class="md"></div><div class="md"></div><div class="md mw">1</div>
      <div class="md mw">2</div><div class="md">3</div><div class="md">4</div><div class="md">5</div><div class="md">6</div><div class="md">7</div><div class="md mw">8</div>
      <div class="md mw">9</div><div class="md">10</div><div class="md">11</div><div class="md">12</div><div class="md">13</div><div class="md">14</div><div class="md mw">15</div>
      <div class="md mw">16</div><div class="md">17</div><div class="md">18</div><div class="md">19</div><div class="md">20</div><div class="md">21</div><div class="md mw">22</div>
      <div class="md mw">23</div><div class="md">24</div><div class="md">25</div><div class="md">26</div><div class="md">17</div><div class="md">28</div><div class="md mw">29</div>
    </div>
  </section>

  <footer class="footer">
    <div class="footer-brand"><div class="name">VERDA</div><div class="sub">CONSTRUCTION LTD</div></div>
    <div class="footer-item"><b>T</b>: +2348001234567</div>
    <div class="footer-item"><b>E</b>: info@verdabuild.com</div>
    <div class="footer-item"><b>W</b>: www.verdabuild.com</div>
    <div class="footer-item"><b>A</b>: Palmgrove Street, Off Harbour Crescent, Central District, Abuja Nigeria</div>
  </footer>
</main>
</body>
</html>
```